U.S. Popcorn company needs business cards

We are a popcorn company that manufactures popcorn and sells it to grocery stores worldwide. Our theme is "Americana" and our logo is U.S. route 66 which is the most famous highway in the U.S.

We would like the design to be simple and to use both sides. On the back side we would like to see just the logo and website. The front would be normal details

Target Market(s)

Wholesalers, grocers and distributors

Industry/Entity Type

Manufacture

Contact Information for Business Card

Business name: Prairie Lantern Popcorn
Phone: +1 555 308 4726
Email: Dale@prairielanternpopcorn.com
website: www.prairielanternpopcorn.com
Tag Line: "Fresh from the kettle"
Name: Dale Whitcombe
Title: Founder/President

Requirements
Must have
• Either this design should be fun or clean and simple. I will let you show me your thougths.
Nice to have
• Anything that ties in the real Hwy Route 66.
• Colors might need to be red, white and blue incorporated.
Should not have
• Not be too busy.

```html
<!DOCTYPE html>
<html lang="en">
<head>
<meta charset="utf-8">
<title>Prairie Lantern Popcorn – Business Card</title>
<link href="https://fonts.googleapis.com/css2?family=Source+Sans+3:ital,wght@0,400;0,600;0,700;1,700&display=swap" rel="stylesheet">
<style>
  :root {
    --navy: #0b2866;
    --red: #e3202c;
    --white: #ffffff;
    --grey: #555a63;
    --rule: #2d4a86;
    --stage: #ecebe8;
  }
  * { box-sizing: border-box; margin: 0; padding: 0; }
  html, body {
    width: 1200px; height: 987px; overflow: hidden;
    background: var(--stage);
    font-family: "Source Sans 3", "Myriad Pro", Arial, sans-serif;
  }
  .card {
    position: absolute; left: 293px; width: 615px; height: 350px;
    overflow: hidden;
    box-shadow: 0 3px 8px rgba(0,0,0,.25);
  }
  .card--front { top: 130px; background: var(--white); }
  .card--back { top: 506px; background: var(--navy); }

  .brand {
    position: absolute; display: flex; align-items: center; gap: 10px;
    font-weight: 700; line-height: 1.05; white-space: nowrap;
  }
  .brand__dot { width: 20px; height: 20px; border-radius: 50%; flex: none; }
  .card--front .brand { left: 392px; top: 92px; color: var(--navy); font-size: 23px; }
  .card--front .brand__dot { background: var(--red); }
  .card--back .brand { left: 418px; top: 234px; color: var(--white); font-size: 20px; }
  .card--back .brand__dot { background: var(--white); width: 17px; height: 17px; }

  .person { position: absolute; left: 30px; top: 167px; }
  .person__name { color: var(--navy); font-size: 23px; font-weight: 600; line-height: 1.1; }
  .person__title { color: var(--red); font-size: 16.5px; font-weight: 400; margin-top: 3px; }

  .divider {
    position: absolute; left: 30px; top: 223px; width: 544px; height: 1.5px;
    background: var(--rule);
  }

  .contacts { position: absolute; left: 32px; top: 235px; list-style: none; }
  .contacts li {
    display: flex; align-items: center; gap: 9px;
    color: var(--grey); font-size: 16px; height: 23.5px;
  }
  .contacts svg { width: 14px; height: 14px; fill: var(--navy); flex: none; }

  .stripe { position: absolute; left: 0; top: 0; width: 615px; height: 350px; }
  .tagline {
    position: absolute; right: 26px; top: 322px;
    color: var(--white); font-size: 17.5px; font-weight: 700; font-style: italic;
  }
</style>
</head>
<body>

<section class="card card--front" aria-label="Business card front">
  <div class="brand">
    <span class="brand__dot"></span>
    <span>Prairie Lantern<br>Popcorn</span>
  </div>

  <div class="person">
    <p class="person__name">Dale Whitcombe</p>
    <p class="person__title">Founder/President</p>
  </div>

  <div class="divider"></div>

  <ul class="contacts">
    <li>
      <svg viewBox="0 0 16 16" aria-hidden="true"><path d="M3.6 1.2l2.3 2.6c.4.4.4 1 0 1.4L4.7 6.4c.9 2 2.6 3.9 4.9 4.9l1.2-1.2c.4-.4 1-.4 1.4 0l2.6 2.3c.4.4.4 1 0 1.4l-1.3 1.3C10.8 16.4 -.4 5.2 .9 2.5L2.2 1.2c.4-.4 1-.4 1.4 0z"/></svg>
      +1 555 308 4726
    </li>
    <li>
      <svg viewBox="0 0 16 16" aria-hidden="true"><path d="M1 3h14v1.2L8 9 1 4.2z"/><path d="M1 5.6l7 4.8 7-4.8V13H1z"/></svg>
      Dale@prairielanternpopcorn.com
    </li>
    <li>
      <svg viewBox="0 0 16 16" aria-hidden="true"><path d="M8 .5a7.5 7.5 0 1 0 0 15A7.5 7.5 0 0 0 8 .5zm-1 2.3c.8.4.5 1.5 1.4 1.9.9.4 1.6-.2 2.2.6.5.7-.4 1.3-1.3 1.5-1 .2-1.7 1-1.4 2 .3 1 1.5 1 1.6 2.1.1 1.1-.8 2-1.7 2.3-.2-1.3-1.1-2.1-1.9-2.8-.9-.7-1.2-1.8-.6-2.7-1.2-.2-2.1-.9-2.5-1.9A6 6 0 0 1 7 2.8z"/></svg>
      www.prairielanternpopcorn.com
    </li>
  </ul>

  <svg class="stripe" viewBox="0 0 615 350" aria-hidden="true">
    <polygon points="0,322 390,322 378,338 0,338" fill="var(--red)"/>
    <polygon points="390,316 615,316 615,350 0,350 0,342 366,342" fill="var(--navy)"/>
  </svg>
  <p class="tagline">Fresh from the kettle</p>
</section>

<section class="card card--back" aria-label="Business card back">
  <div class="brand">
    <span class="brand__dot"></span>
    <span>Prairie Lantern<br>Popcorn</span>
  </div>
</section>

</body>
</html>
```